Media Services Start-up -- Corporate Website and Logo Design. Inspiration required!

We need a logo design and corporate website design, including coding, for our start-up business.
Vennatra’s value proposition is based on bringing together media content from a vast number of geographies globally, adding human and AI curation, translation and editing, and delivering the content using tailored customer interfaces. On the one hand, the business brings together media coverage from all over the world, and on the other it brings together content, human skills and technology to deliver a supreme customer experience.
Vennatra is a B2B media monitoring and analytics business with emphasis on global customers. Vennatra's service offering is centred around sourcing media content from different markets, processing, storing and delivering the content and insights derived from it using an online platform / mobile app.
The messaging we want to create through the logo is:
- Global scope
- Speed of delivery
- Cost-efficiency
- Multi-lingual
- Tailor-made
- Trustworthy
Target Market(s)
Business to business, PR / Communications, Media, Marketing
Logo Text
Vennatra
Coding
Coded - Design and coding required
Number of Pages Required
5+ page
Font styles to use
Other font styles liked:
- See Design Brief for details
Colors
Designer to choose colors to be used in the design.

```html
<!DOCTYPE html>
<html lang="en">
<head>
<meta charset="utf-8">
<title>Vennatra — Global Media Intelligence</title>
<link href="https://fonts.googleapis.com/css2?family=Roboto:wght@400;500;700&display=swap" rel="stylesheet">
<style>
  :root{
    --ink:#0d0d0d;
    --bar:#141414;
    --white:#ffffff;
    --soft:#e6e6e6;
    --field:#4d4d4d;
    --frame:#cfcfcf;
    --blue:#0674d6;
  }
  *{box-sizing:border-box;margin:0;padding:0}
  html,body{width:1200px;height:544px;overflow:hidden;background:var(--ink)}
  body{font-family:'Roboto',sans-serif;color:var(--white);position:relative}
  .hero-visual{position:absolute;left:0;top:0;width:1200px;height:508px;
    background:
      radial-gradient(circle at 700px 330px,#6b6b6b 0,#3a3a3a 90px,#232323 170px,rgba(20,20,20,0) 260px),
      radial-gradient(ellipse at 120px 330px,#2e2e2e 0,rgba(20,20,20,0) 260px),
      linear-gradient(180deg,#1c1c1c 0,#161616 60%,#0b0b0b 100%);}
  .site-header{position:absolute;left:0;top:0;width:1200px;height:85px;background:rgba(16,16,16,.92)}
  .logo{position:absolute;left:140px;top:12px;font-size:44px;font-weight:700;color:var(--soft);letter-spacing:-.5px}
  .contact{position:absolute;top:31px;display:flex;align-items:center;gap:6px;font-size:14px;white-space:nowrap}
  .contact.phone{left:616px}
  .contact.mail{left:754px}
  .account{position:absolute;left:919px;top:25px;height:32px;width:96px;border:1px solid var(--soft);display:flex}
  .account .edit{width:31px;border-right:1px solid var(--soft);display:flex;align-items:center;justify-content:center}
  .account .label{flex:1;display:flex;align-items:center;justify-content:center;font-size:15px}
  .menu{position:absolute;left:1026px;top:25px;width:32px;height:32px;border:1.5px solid var(--white);display:flex;flex-direction:column;justify-content:center;align-items:center;gap:4px}
  .menu span{display:block;width:20px;height:3px;background:var(--white)}
  .intro{position:absolute;left:140px;top:168px;width:350px}
  .intro h1{font-size:32px;line-height:38px;font-weight:700;text-transform:uppercase}
  .intro p{margin-top:16px;font-size:16px;line-height:24.7px;letter-spacing:.3px}
  .cta{position:absolute;left:141px;top:374px;width:175px;height:40px;background:var(--white);color:var(--ink);font-size:15.5px;display:flex;align-items:center;justify-content:center}
  .cta::after{content:"";position:absolute;left:4px;top:4px;width:175px;height:40px;border:1px solid #777;z-index:-1}
  .lead-form{position:absolute;left:753px;top:128px;width:304px;height:337px;border:7px solid var(--frame);background:var(--ink);padding:0 13px}
  .lead-form h2{font-size:21px;font-weight:700;margin-top:27px;margin-bottom:27px;white-space:nowrap}
  .field{height:42px;background:var(--field);margin-bottom:15px;display:flex;align-items:center;gap:6px;padding-left:9px;font-size:12.5px;color:#f2f2f2}
  .submit{height:43px;background:var(--blue);display:flex;align-items:center;justify-content:center;font-size:17px;font-weight:700;margin-top:20px}
  .field:last-of-type{margin-bottom:0}
  .site-footer{position:absolute;left:0;top:508px;width:1200px;height:36px;background:var(--blue);font-size:13px}
  .site-footer .copy{position:absolute;left:141px;top:10px}
  .social{position:absolute;right:142px;top:11px;display:flex;gap:9px}
  .social span{width:15px;height:15px;border-radius:50%;background:var(--white)}
</style>
</head>
<body>
  <div class="hero-visual" role="img" aria-label="Dark cityscape at night with a glowing globe, a businessman viewed from behind and network lines connecting media icons"></div>

  <header class="site-header">
    <div class="logo">Vennatra</div>
    <div class="contact phone">
      <svg width="14" height="14" viewBox="0 0 24 24" fill="#fff"><path d="M6.6 10.8a15 15 0 0 0 6.6 6.6l2.2-2.2c.3-.3.7-.4 1-.2 1.1.4 2.3.6 3.6.6.6 0 1 .4 1 1V20c0 .6-.4 1-1 1A17 17 0 0 1 3 4c0-.6.4-1 1-1h3.5c.6 0 1 .4 1 1 0 1.3.2 2.5.6 3.6.1.3 0 .7-.2 1z"/></svg>
      +1 555 014 2290
    </div>
    <div class="contact mail">
      <svg width="20" height="14" viewBox="0 0 20 14" fill="none" stroke="#fff" stroke-width="1.4"><rect x="1" y="1" width="18" height="12"/><path d="M1 1l9 7 9-7M1 13l6-6M19 13l-6-6"/></svg>
      info@vennatra.com
    </div>
    <div class="account">
      <div class="edit"><svg width="15" height="15" viewBox="0 0 16 16" fill="none" stroke="#fff" stroke-width="1.6"><path d="M13 9v5H2V3h5"/><path d="M6 10l1-3 6-6 2 2-6 6z"/></svg></div>
      <div class="label">Sign In</div>
    </div>
    <div class="menu"><span></span><span></span><span></span></div>
  </header>

  <section class="intro">
    <h1>Delivering Global Media Intelligence</h1>
    <p>Vennatra is an international media intelligence service provider. We help communications teams build and operate truly global media monitoring and measurement programmes.</p>
  </section>
  <a class="cta">CONTACT US TODAY</a>

  <form class="lead-form">
    <h2>Learn More About Vennatra</h2>
    <div class="field"><svg width="14" height="14" viewBox="0 0 16 16" fill="#fff"><circle cx="8" cy="4.5" r="3.5"/><path d="M1 16c0-4 3-6.5 7-6.5s7 2.5 7 6.5z"/></svg>Your Name*</div>
    <div class="field"><svg width="15" height="11" viewBox="0 0 20 14" fill="none" stroke="#fff" stroke-width="1.8"><rect x="1" y="1" width="18" height="12"/><path d="M1 1l9 7 9-7"/></svg>Your Email*</div>
    <div class="field"><svg width="14" height="14" viewBox="0 0 24 24" fill="#fff"><path d="M6.6 10.8a15 15 0 0 0 6.6 6.6l2.2-2.2c.3-.3.7-.4 1-.2 1.1.4 2.3.6 3.6.6.6 0 1 .4 1 1V20c0 .6-.4 1-1 1A17 17 0 0 1 3 4c0-.6.4-1 1-1h3.5c.6 0 1 .4 1 1 0 1.3.2 2.5.6 3.6.1.3 0 .7-.2 1z"/></svg>Your Phone*</div>
    <div class="submit">GET STARTED</div>
  </form>

  <footer class="site-footer">
    <div class="copy">Copyright © 2019 Vennatra. All Rights Reserved.</div>
    <div class="social"><span></span><span></span><span></span></div>
  </footer>
</body>
</html>
```